Very new and innovative Web design for Property managers of Vacation rentals

We are looking for a new website design for travel agencies and property managers specialised on vacation rentals business, holiday villas and apartments.

The end users of this website are travellers who are looking for a vacation home for their next holiday: this is the reason why the website must be easy to use, attractive, professional, possibly elegant and focused on get new reservations.

This is a draft of our current website: https://intro3.kelumsito.com/
Please consider that we would like to have proposals with a totally different and innovative layout, surprise us!

These are the pages of the website:
• Homepage: feel free to redesign all the homepage as you wish, surprise us with something very new! Please consider that Property manager/Travel agencies usually want to have the opportunity to put in evidence groups of houses with specific characteristics (eg. villas with private swimming pool, apartment in big/small towns, villas with air co, etc…), destinations and tourist areas, and sometimes experiences or activities (please consider that the website layout must be suitable even if some of the previous sections are not used).
• Search page: we’d like to organise the results of the search page in three different ways:
o Grid
o Map
o List
• Property page: to illustrate the characteristics, descriptions, images, …. of the property. It is very important to put in evidence images of the property and to maintain the booking form (and the other call to action bottom – eg. whatsapp) always visible
• Custom pages: static pages composed usually by text, images and call to actions
• Contact us (general form)
• Info request (specific of a property form)
• Booking process
• Blog, organised in four pages:
o Home Page – introduction to the blog
o List of articles
o Single article
o Site Map (presentation of categories and sub-categories)

If possible, we’d prefer to receive the material in Adobe XD or similar so that we can obtain the three versions:
- smartphone
- tablet
- desktop

The website will be then developed in Bootstrap: as a result we’ll need the icons in SVG format (or the library used)

In attachment you can find the map of the website pages

```html
<!DOCTYPE html>
<html lang="en">
<head>
<meta charset="utf-8">
<title>Custom Page – Staylane</title>
<link href="https://fonts.googleapis.com/css2?family=Poppins:wght@300;400;500;600&family=PT+Sans+Narrow:wght@400;700&display=swap" rel="stylesheet">
<style>
:root{
  --green:#12c08a;
  --green-dark:#0fa676;
  --ink:#222;
  --muted:#6a6a6a;
  --footer:#1d1b1c;
  --footer-text:#e6e6e6;
  --line:#3a3839;
}
*{box-sizing:border-box;margin:0;padding:0}
html,body{width:1200px;height:2925px;overflow:hidden;background:#fff;font-family:'Poppins',sans-serif;color:var(--ink)}
.page{position:relative;width:1200px;height:2925px}
.abs{position:absolute}

/* header */
.topbar{position:absolute;right:0;top:0;width:328px;height:32px;background:var(--green);clip-path:polygon(0 0,100% 0,100% 100%,32px 100%);display:flex;align-items:center;gap:22px;padding-left:46px;font-size:10px;font-weight:600;color:#fff;letter-spacing:.2px}
.topbar span{display:flex;align-items:center;gap:5px}
.brand{position:absolute;left:99px;top:24px;display:flex;align-items:center;gap:8px;font-size:24px;font-weight:400;color:var(--ink)}
.brand .mark{width:26px;height:26px;background:var(--green);border-radius:50%}
.nav{position:absolute;top:47px;left:0;width:1200px;font-size:11px;color:#333;letter-spacing:.3px}
.nav a{position:absolute;text-decoration:none;color:inherit}
.nav a.active{color:var(--green);font-weight:500}

.hero{position:absolute;left:0;top:87px;width:1200px;height:244px;background:linear-gradient(100deg,#3d3a33 0%,#4a5a52 30%,#2f4a44 55%,#5a4632 80%,#3b2f26 100%);display:flex;align-items:center;justify-content:center}
.hero h1{font-family:'PT Sans Narrow',sans-serif;font-weight:700;font-size:42px;color:#fff;letter-spacing:.5px;margin-top:40px}

.crumbs{position:absolute;left:93px;top:366px;font-size:11px;color:#888}
.crumbs b{font-weight:400;color:var(--ink)}

/* feature rows */
.feature .photo{position:absolute;width:432px;height:292px;border-radius:3px}
.feature .kicker{position:absolute;font-family:'PT Sans Narrow',sans-serif;font-size:23px;color:#222}
.feature h2{position:absolute;font-family:'PT Sans Narrow',sans-serif;font-weight:400;font-size:43px;color:#222;white-space:nowrap}
.feature p{position:absolute;width:560px;font-size:14px;line-height:22.6px;color:var(--muted);font-weight:300}

/* footer */
.footer{position:absolute;left:0;top:2312px;width:1200px;height:613px;background:var(--footer);color:var(--footer-text)}
.footer .brand-f{position:absolute;left:96px;top:100px;display:flex;align-items:center;gap:10px;font-size:26px;font-weight:500;letter-spacing:1px;color:#fff}
.footer .brand-f .mark{width:28px;height:28px;background:var(--green);border-radius:50%}
.newsletter{position:absolute;left:95px;top:166px;font-size:12.5px;letter-spacing:.6px;font-weight:500}
.newsletter-line{position:absolute;left:95px;top:192px;width:209px;height:1px;background:#ddd}
.about{position:absolute;left:95px;top:218px;width:300px;font-size:12.5px;line-height:18px;letter-spacing:.4px;color:#ddd}
.col-title{position:absolute;font-size:15px;color:var(--green);letter-spacing:1px;font-weight:500}
.nav-list{position:absolute;left:518px;top:114px;list-style:none;font-size:12.5px;letter-spacing:.8px;line-height:34.5px;color:#ddd}
.post{position:absolute;left:791px;width:300px;height:62px}
.post .thumb{position:absolute;left:0;top:0;width:71px;height:62px;border-radius:2px}
.post h4{position:absolute;left:81px;top:4px;width:225px;font-size:12px;font-weight:600;color:var(--green);line-height:15px}
.post time{position:absolute;left:81px;top:46px;font-size:12px;color:#ddd}
.contact{position:absolute;top:368px;display:flex;align-items:center;gap:12px}
.contact strong{display:block;font-size:14px;color:var(--green);letter-spacing:1px;font-weight:600}
.contact span{display:block;font-size:14.5px;letter-spacing:.8px;color:#eee}
.vline{position:absolute;top:338px;width:1px;height:120px;background:var(--line)}
.hline{position:absolute;left:95px;top:458px;width:1012px;height:1px;background:var(--line)}
.legal{position:absolute;left:0;top:481px;width:1200px;text-align:center;font-size:12px;letter-spacing:.8px;font-weight:500;line-height:19px}
.legal em{font-style:normal;color:var(--green)}
.social{position:absolute;top:538px;left:578px;display:flex;gap:6px;align-items:center}
.social .dot{width:16px;height:16px;border-radius:50%;background:#fff}
.social .badge{width:56px;height:14px;background:#3b6fd8;border-radius:2px}
</style>
</head>
<body>
<div class="page">

  <header>
    <div class="topbar">
      <span><svg width="11" height="11" viewBox="0 0 12 12" fill="none" stroke="#fff" stroke-width="1.3"><circle cx="6" cy="4" r="2.6"/><path d="M1.5 11.5c.5-2.6 2.3-4 4.5-4s4 1.4 4.5 4"/></svg>LOGIN</span>
      <span><svg width="12" height="11" viewBox="0 0 12 11" fill="none" stroke="#fff" stroke-width="1.3"><path d="M6 10 1.5 5.6A2.6 2.6 0 0 1 6 2.3a2.6 2.6 0 0 1 4.5 3.3Z"/></svg>WHISHLIST</span>
      <span>EN ˅</span>
    </div>
    <div class="brand"><div class="mark"></div>Staylane</div>
    <nav class="nav">
      <a class="active" style="left:661px">HOME</a>
      <a style="left:742px">SEARCH</a>
      <a style="left:833px">PROPERTY</a>
      <a style="left:939px">CUSTOM</a>
      <a style="left:1033px">CONTACT US</a>
    </nav>
  </header>

  <section class="hero" role="img" aria-label="Canal with boats and historic waterfront buildings">
    <h1>CUSTOM PAGE</h1>
  </section>

  <div class="crumbs">Home Page &nbsp;/&nbsp; <b>Custom Page</b></div>

  <main>
    <article class="feature">
      <div class="photo" style="left:94px;top:437px;background:linear-gradient(180deg,#16264f 0%,#2d3a66 40%,#a8864f 75%,#5a3e22 100%)" role="img" aria-label="Domed basilica lit up at dusk"></div>
      <div class="kicker" style="left:553px;top:456px">I explain to you</div>
      <h2 style="left:553px;top:484px">Ducimus Qui Praesentium</h2>
      <p style="left:553px;top:558px">Nam libero tempore, cum soluta nobis est eligendi optio cumque nihil impedit quo minus id quod maxime placeat facere possimus, omnis voluptas assumenda est, omnis dolor repellendus. Temporibus autem quibusdam et aut officiis debitis aut rerum necessitatibus saepe eveniet ut et voluptates repudiandae sint et molestiae non recusandae. Itaque earum rerum hic tenetur a sapiente delectus, ut aut reiciendis voluptatibus maiores alias consequatur aut perferendis doloribus asperiores repellat.</p>
    </article>

    <article class="feature">
      <div class="photo" style="left:96px;top:807px;background:linear-gradient(180deg,#2f6fd0 0%,#8fb6e6 40%,#e7e2d6 70%,#5aa83a 100%)" role="img" aria-label="Leaning bell tower and cathedral under a blue sky"></div>
      <div class="kicker" style="left:557px;top:851px">I explain to you</div>
      <h2 style="left:557px;top:879px">Ducimus Qui Praesentium</h2>
      <p style="left:557px;top:941px">Nam libero tempore, cum soluta nobis est eligendi optio cumque nihil impedit quo minus id quod maxime placeat facere possimus, omnis voluptas assumenda est, omnis dolor repellendus. Temporibus autem quibusdam et aut officiis debitis aut rerum necessitatibus saepe eveniet ut et voluptates repudiandae sint et molestiae non recusandae.</p>
    </article>

    <article class="feature">
      <div class="photo" style="left:94px;top:1182px;background:linear-gradient(180deg,#e8a074 0%,#d98a6a 35%,#4fb0c0 65%,#2a8fa6 100%)" role="img" aria-label="Traveller relaxing in a resort swimming pool"></div>
      <div class="kicker" style="left:555px;top:1207px">I explain to you</div>
      <h2 style="left:555px;top:1235px">Ducimus Qui Praesentium</h2>
      <p style="left:555px;top:1297px">Nam libero tempore, cum soluta nobis est eligendi optio cumque nihil impedit quo minus id quod maxime placeat facere possimus, omnis voluptas assumenda est, omnis dolor repellendus. Temporibus autem quibusdam et aut officiis debitis aut rerum necessitatibus saepe eveniet ut et voluptates repudiandae sint et molestiae non recusandae.</p>
    </article>

    <article class="feature">
      <div class="photo" style="left:93px;top:1547px;background:linear-gradient(180deg,#6f93c4 0%,#a9bfd8 30%,#a0846a 55%,#6b5a48 80%,#3a4a30 100%)" role="img" aria-label="Ancient amphitheatre at sunset"></div>
      <div class="kicker" style="left:557px;top:1582px">I explain to you</div>
      <h2 style="left:557px;top:1610px">Ducimus Qui Praesentium</h2>
      <p style="left:557px;top:1672px">Nam libero tempore, cum soluta nobis est eligendi optio cumque nihil impedit quo minus id quod maxime placeat facere possimus, omnis voluptas assumenda est, omnis dolor repellendus. Temporibus autem quibusdam et aut officiis debitis aut rerum necessitatibus saepe eveniet ut et voluptates repudiandae sint et molestiae non recusandae.</p>
    </article>

    <article class="feature">
      <div class="photo" style="left:94px;top:1911px;background:linear-gradient(180deg,#9fb3c8 0%,#5e7060 35%,#3d5a5a 60%,#1f3450 100%)" role="img" aria-label="Lakeside alpine village beneath mountains"></div>
      <div class="kicker" style="left:560px;top:1950px">I explain to you</div>
      <h2 style="left:560px;top:1978px">Ducimus Qui Praesentium</h2>
      <p style="left:561px;top:2040px">Nam libero tempore, cum soluta nobis est eligendi optio cumque nihil impedit quo minus id quod maxime placeat facere possimus, omnis voluptas assumenda est, omnis dolor repellendus. Temporibus autem quibusdam et aut officiis debitis aut rerum necessitatibus saepe eveniet ut et voluptates repudiandae sint et molestiae non recusandae.</p>
    </article>
  </main>

  <footer class="footer">
    <div class="brand-f"><div class="mark"></div>Staylane</div>
    <div class="newsletter">Subscribe to our Newsletter</div>
    <div class="newsletter-line"></div>
    <svg class="abs" style="left:325px;top:185px" width="40" height="14" viewBox="0 0 40 14" fill="none" stroke="#12c08a" stroke-width="1.2"><path d="M0 7h38M32 1l6 6-6 6"/></svg>
    <p class="about">Our range of services is very large, and we are constantly expanding it.</p>

    <div class="col-title" style="left:516px;top:77px">Navigation</div>
    <ul class="nav-list">
      <li>Last Minute</li><li>Special Offers</li><li>Experience</li><li>Contact Us</li>
    </ul>

    <div class="col-title" style="left:791px;top:77px">Recent posts</div>
    <div class="post" style="top:116px">
      <div class="thumb" style="background:linear-gradient(180deg,#6f8a4a,#3a9ac0)" role="img" aria-label="Garden pool with sun umbrella"></div>
      <h4>Which construction tool is better to choose?</h4>
      <time>2 November, 2020</time>
    </div>
    <div class="post" style="top:201px">
      <div class="thumb" style="background:linear-gradient(180deg,#7a5a40,#8fa0b8)" role="img" aria-label="Room with table tennis table"></div>
      <h4>Which construction tool is better to choose?</h4>
      <time>2 November, 2020</time>
    </div>

    <div class="contact" style="left:120px">
      <svg width="32" height="32" viewBox="0 0 24 24" fill="#12c08a"><path d="M6.6 10.8a15.5 15.5 0 0 0 6.6 6.6l2.2-2.2a1 1 0 0 1 1-.25 11.4 11.4 0 0 0 3.6.57 1 1 0 0 1 1 1V20a1 1 0 0 1-1 1A17 17 0 0 1 3 4a1 1 0 0 1 1-1h3.5a1 1 0 0 1 1 1c0 1.25.2 2.45.57 3.57a1 1 0 0 1-.25 1z"/></svg>
      <div><strong>Call us</strong><span>+1 555 014 2290 (USA)</span></div>
    </div>
    <div class="vline" style="left:434px"></div>
    <div class="contact" style="left:485px">
      <svg width="40" height="30" viewBox="0 0 40 30" fill="none" stroke="#12c08a" stroke-width="2.2"><rect x="1.5" y="1.5" width="37" height="27" rx="2"/><path d="M2 3l18 14L38 3"/></svg>
      <div><strong>Write to us</strong><span>hello@staylane-mail.com</span></div>
    </div>
    <div class="vline" style="left:763px"></div>
    <div class="contact" style="left:823px">
      <svg width="30" height="42" viewBox="0 0 30 42" fill="none" stroke="#12c08a" stroke-width="2.2"><path d="M15 40S2 24 2 14a13 13 0 0 1 26 0c0 10-13 26-13 26Z"/><circle cx="15" cy="14" r="5"/></svg>
      <div><strong>Office location</strong><span>12 Harbor Lane, Westbrook, NY 10990</span></div>
    </div>
    <div class="hline"></div>

    <div class="legal">
      <div>Privacy Policies &nbsp;&nbsp;/&nbsp;&nbsp; Reservation Policies &nbsp;&nbsp;/&nbsp;&nbsp; Cookie Policy</div>
      <div>Copyright © 2021 Staylane. All Rights Reserved. <em>Powered by Staylane</em></div>
    </div>
    <div class="social"><div class="dot"></div><div class="badge"></div></div>
  </footer>

</div>
</body>
</html>
```